Small butcher shop from Austria needs great powerpoint presentation

We are looking for a powerpoint template for our new CI - it should be modern and clear.

Logo (2 Versions), Slogan, Business Card and Car-Wrap-Design already exist. (See documents below.)

We won't use much text. About 50% of the presentation should be pictures, included in different ways.

We are a family business in Upper Austria, only process animals from farms in the immediate vicinity, produce the products by hand, value animal welfare and short transport routes and avoid packaging as much as possible.

The design should be modern and clear.

Sans Serif

• Use the red color sparingly. Only use sans serif fonts (Myriad Pro - if possible). The logo needs to be on first and last page only.

```html
<!DOCTYPE html>
<html lang="en">
<head>
<meta charset="utf-8">
<title>Halder Fleischhauerei – Presentation Template</title>
<link rel="stylesheet" href="https://fonts.googleapis.com/css2?family=Source+Sans+3:wght@300;400;600;700;900&family=Montserrat:wght@800;900&display=swap">
<style>
:root{
  --stage:#c6c6c6;
  --wine:#8e1b2a;
  --wine-dark:#6d1320;
  --white:#ffffff;
  --ink:#1d1d1d;
  --grey:#a9a9a9;
  --grey-light:#d9d9d9;
  --text:#333333;
}
*{box-sizing:border-box;margin:0;padding:0}
html,body{width:1200px;height:1200px;overflow:hidden;background:var(--stage)}
body{position:relative;font-family:"Source Sans 3",sans-serif;color:var(--text)}
.slide{position:absolute;background:var(--white);box-shadow:0 2px 6px rgba(0,0,0,.18);overflow:hidden}
.abs{position:absolute}

/* cover */
.cover{left:178px;top:52px;width:860px;height:483px;background:var(--wine)}
.cover-art{left:118px;top:28px;width:690px;height:400px;background:var(--white);border-radius:120px 160px 40px 60px}
.cover-meadow{left:0;top:425px;width:860px;height:58px;background:var(--white)}
.cut-word{font-family:"Montserrat",sans-serif;font-weight:900;color:var(--wine);white-space:nowrap;transform-origin:left top}
.brand{left:0;width:826px;text-align:center;color:var(--wine)}
.brand-name{top:150px;font-weight:600;font-size:66px;letter-spacing:3px;line-height:1}
.brand-sub{top:244px;font-size:12px;letter-spacing:4.5px;color:#555;font-weight:400}
.cover-url{top:446px;width:860px;font-size:21px;font-weight:600;letter-spacing:12px}

/* shared footer */
.footer{left:16px;right:12px;bottom:7px;height:14px;display:flex;align-items:center;gap:10px}
.foot-url{font-size:7.5px;letter-spacing:1px;color:var(--ink);white-space:nowrap;flex:none}
.foot-line{flex:1;height:1px;background:var(--wine)}
.foot-num{flex:none;width:11px;height:11px;margin:0 2px 0 4px;background:var(--wine);transform:rotate(45deg)}
.foot-num span{display:block;transform:rotate(-45deg);color:#fff;font-size:6.5px;text-align:center;line-height:11px}

/* contents */
.contents{left:142px;top:575px;width:462px;height:258px}
.contents-rail{left:0;top:0;width:105px;height:258px;background:linear-gradient(90deg,#fff 80%,#eee)}
.contents-title{left:14px;top:248px;transform:rotate(-90deg);transform-origin:left top;white-space:nowrap;line-height:1}
.contents-title .light{font-size:38px;font-weight:300;color:var(--grey);letter-spacing:2px}
.contents-title .bold{font-family:"Montserrat",sans-serif;font-size:40px;font-weight:900;color:var(--ink)}
.contents-grid{left:110px;top:21px;width:333px;height:228px;display:grid;grid-template-columns:1fr 1fr;grid-template-rows:repeat(3,1fr)}
.entry{display:flex;align-items:center;gap:3px;padding-left:6px;border-bottom:1px solid var(--grey-light)}
.entry:nth-child(odd){border-right:1px solid var(--grey-light)}
.entry:nth-child(n+5){border-bottom:none}
.entry-num{font-family:"Montserrat",sans-serif;font-weight:900;font-size:44px;color:var(--grey);line-height:1;width:30px}
.entry-head{font-family:"Montserrat",sans-serif;font-weight:800;font-size:13px;color:var(--wine);line-height:1.1}
.entry-text{font-size:5.8px;line-height:1.4;text-transform:uppercase;color:#444;margin-top:2px;width:100px}

/* services */
.services{left:620px;top:575px;width:461px;height:258px}
.services-title{left:0;top:26px;width:461px;text-align:center;font-family:"Montserrat",sans-serif;font-weight:900;font-size:21px;color:var(--wine)}
.services-intro{left:48px;top:57px;width:370px;font-size:7px;line-height:1.4;color:var(--ink)}
.service{top:103px;width:88px}
.service-frame{position:relative;width:86px;height:61px}
.service-frame::before{content:"";position:absolute;left:3px;top:3px;width:83px;height:58px;background:var(--wine)}
.service-photo{position:absolute;left:0;top:0;width:83px;height:58px;border:2px solid var(--wine);background:#fff;padding:3px}
.service-photo div{width:100%;height:100%}
.service-name{margin-top:16px;font-weight:700;font-size:8px;color:var(--wine);text-align:center;padding-right:10px}
.service-text{margin-top:2px;font-size:6.4px;line-height:1.4;color:var(--ink)}

/* gallery */
.gallery{left:142px;top:874px;width:462px;height:259px}
.gallery-title{left:0;top:10px;width:455px;text-align:center;font-family:"Montserrat",sans-serif;font-weight:900;font-size:32px;color:var(--ink);background:linear-gradient(90deg,#1d1d1d 30%,var(--wine-dark));-webkit-background-clip:text;background-clip:text;-webkit-text-fill-color:transparent}
.ph{position:absolute}

/* why us */
.why{left:618px;top:874px;width:461px;height:259px}
.why-photo{left:0;top:0;width:461px;height:142px;background:linear-gradient(180deg,#2a2d36,#5a2a26 55%,#7a3a2a)}
.why-title{left:0;top:97px;width:461px;text-align:center;font-family:"Montserrat",sans-serif;font-weight:900;font-size:48px;color:#fff;line-height:1}
.why-text{left:84px;top:153px;width:293px;text-align:center;font-size:7px;line-height:1.4;color:var(--ink)}
.why-flourish{left:193px;top:204px;width:76px;height:18px;background:var(--grey-light);border-radius:9px}
</style>
</head>
<body>

<section class="slide cover">
  <div class="abs cover-art" role="img" aria-label="White cow silhouette standing in grass with dashed butcher cut lines, over a faint meat doodle pattern"></div>
  <div class="abs cover-meadow"></div>
  <span class="abs cut-word" style="left:147px;top:120px;font-size:25px;transform:rotate(-24deg)">TASTY</span>
  <span class="abs cut-word" style="left:186px;top:262px;font-size:23px;transform:rotate(-55deg)">HEALTHY</span>
  <span class="abs cut-word" style="left:545px;top:134px;font-size:15px;transform:rotate(-62deg)">YUMMY</span>
  <span class="abs cut-word" style="left:716px;top:104px;font-size:25px;transform:rotate(48deg)">TASTY</span>
  <div class="abs brand brand-name">HALDER</div>
  <div class="abs brand brand-sub">FLEISCHHAUEREI</div>
  <div class="abs brand cover-url">WWW.HALDER-FLEISCH.AT</div>
</section>

<section class="slide contents">
  <div class="abs contents-rail"></div>
  <div class="abs contents-title"><span class="light">TABLE OF</span><br><span class="bold">CONTENT</span></div>
  <div class="abs contents-grid">
    <div class="entry"><span class="entry-num">1</span><div><div class="entry-head">CONTENT HERE</div><div class="entry-text">Lorem ipsum is simply dummy text of the printing and typesetting industry.</div></div></div>
    <div class="entry"><span class="entry-num">2</span><div><div class="entry-head">CONTENT HERE</div><div class="entry-text">Lorem ipsum is simply dummy text of the printing and typesetting industry.</div></div></div>
    <div class="entry"><span class="entry-num">3</span><div><div class="entry-head">CONTENT HERE</div><div class="entry-text">Lorem ipsum is simply dummy text of the printing and typesetting industry.</div></div></div>
    <div class="entry"><span class="entry-num">4</span><div><div class="entry-head">CONTENT HERE</div><div class="entry-text">Lorem ipsum is simply dummy text of the printing and typesetting industry.</div></div></div>
    <div class="entry"><span class="entry-num">5</span><div><div class="entry-head">CONTENT HERE</div><div class="entry-text">Lorem ipsum is simply dummy text of the printing and typesetting industry.</div></div></div>
    <div class="entry"><span class="entry-num">6</span><div><div class="entry-head">CONTENT HERE</div><div class="entry-text">Lorem ipsum is simply dummy text of the printing and typesetting industry.</div></div></div>
  </div>
</section>

<section class="slide services">
  <h2 class="abs services-title">LOREM IPSUM IS SIMPLY DUMMY</h2>
  <p class="abs services-intro">Lorem Ipsum is simply dummy text of the printing and typesetting industry. Lorem Ipsum has been the industry's standard dummy text ever since the 1500s, when an unknown printer took a galley of type and scrambled it to make a type specimen book.Lorem Ipsum is simply dummy text of the printing and typesetting industry.</p>
  <div class="abs service" style="left:43px">
    <div class="service-frame"><div class="service-photo"><div role="img" aria-label="Raw steak with herbs" style="background:linear-gradient(135deg,#c84a4f,#8e2a2e 60%,#6b8a4a)"></div></div></div>
    <div class="service-name">BUTCHERY</div>
    <div class="service-text">Regional meat and sausage from our own production and conviction.</div>
  </div>
  <div class="abs service" style="left:136px">
    <div class="service-frame"><div class="service-photo"><div role="img" aria-label="Schnitzel plate with fries" style="background:radial-gradient(circle,#e2a44a,#f2e2c8 60%,#fff)"></div></div></div>
    <div class="service-name">SNACK/MENU</div>
    <div class="service-text">Regional meat and sausage from our own production and conviction.</div>
  </div>
  <div class="abs service" style="left:229px">
    <div class="service-frame"><div class="service-photo"><div role="img" aria-label="Garnished stuffed potatoes" style="background:linear-gradient(180deg,#d9b4b0,#c58a5a 60%,#f5f0e8)"></div></div></div>
    <div class="service-name">PLATE SERVICE</div>
    <div class="service-text">Cold and warm dishes, all finely garnished. Picked up or delivered.</div>
  </div>
  <div class="abs service" style="left:322px">
    <div class="service-frame"><div class="service-photo"><div role="img" aria-label="Heart-shaped piece of lean beef" style="background:radial-gradient(circle,#8a1828 35%,#fff 55%)"></div></div></div>
    <div class="service-name">RINDPUR ©</div>
    <div class="service-text">Sausage made from 100% lean beef, according to a unique recipe..</div>
  </div>
  <div class="abs footer"><span class="foot-url">WWW.HALDER-FLEISCH.AT</span><span class="foot-line"></span><span class="foot-num"><span>1</span></span></div>
</section>

<section class="slide gallery">
  <h2 class="abs gallery-title">GALLERY</h2>
  <div class="ph" role="img" aria-label="Trays of canapés" style="left:32px;top:55px;width:108px;height:109px;background:linear-gradient(160deg,#5a3a2a,#c98a5a 50%,#3a2a20)"></div>
  <div class="ph" role="img" aria-label="Tray of breaded cutlets" style="left:32px;top:169px;width:108px;height:59px;background:linear-gradient(160deg,#2a2020,#c7843a 55%,#6a4a2a)"></div>
  <div class="ph" role="img" aria-label="Salami slices with tomatoes and lettuce" style="left:145px;top:55px;width:161px;height:92px;background:linear-gradient(135deg,#d6453a,#e08a80 45%,#a8c870)"></div>
  <div class="ph" role="img" aria-label="Cold cuts platter with eggs and cucumber" style="left:145px;top:152px;width:161px;height:76px;background:linear-gradient(135deg,#b85a4a,#e6b49a 50%,#8ab05a)"></div>
  <div class="ph" role="img" aria-label="Buffet platter" style="left:313px;top:55px;width:54px;height:55px;background:linear-gradient(135deg,#6a4a3a,#d2a070)"></div>
  <div class="ph" role="img" aria-label="Garnished plate" style="left:372px;top:55px;width:56px;height:55px;background:linear-gradient(135deg,#3a3030,#e8d0c0)"></div>
  <div class="ph" role="img" aria-label="Large ham and sausage platter with garnish" style="left:313px;top:115px;width:115px;height:113px;background:radial-gradient(circle,#4a7a3a 15%,#d8a8a0 45%,#7a5a50)"></div>
  <div class="abs footer"><span class="foot-url">WWW.HALDER-FLEISCH.AT</span><span class="foot-line"></span><span class="foot-num"><span>2</span></span></div>
</section>

<section class="slide why">
  <div class="abs why-photo" role="img" aria-label="Smoked hams and sausages hanging in a row"></div>
  <h2 class="abs why-title">WHY US</h2>
  <p class="abs why-text">Lorem Ipsum is simply dummy text of the printing and typesetting industry. Lorem Ipsum has been the industry's standard dummy text ever since the 1500s, when an unknown printer took a galley of type and scrambled it to make a type specimen book. It has survived not only five centuries, but also the leap into electronic typesetting, remaining essentially unchanged.</p>
  <div class="abs why-flourish" role="img" aria-label="Small grey ornamental flourish"></div>
  <div class="abs footer"><span class="foot-url">WWW.HALDER-FLEISCH.AT</span><span class="foot-line"></span><span class="foot-num"><span>3</span></span></div>
</section>

</body>
</html>
```